International sourcing and trading company needs website design on Squarespace

We are international sourcing and trading company based in Brisbane ,Australia. We help our clients to source any products they need to economically produce overseas and we manage the whole production process for them. We want our visual identity to show that we are professional, dynamic, efficient and are able to source any product around the world. Our website will be simply information and advertising website , no ecommerce or any transactions. Please see attached our company logo. We would like our website to have the following sections/pages:

1.Main banner with a simple slogan/sentence to introduce what we do: Let us handle the overseas sourcing and production for you.

2. Post-Covid sourcing and producing management: introducing our competence on managing sourcing and overseas production under the travel restriction and the growing tension on global trading. We will supply the exact wording later on;

3. About us: We are a professional team with mature global sourcing and trading experience. We have branch office in Hong Kong and local resources around all areas in China , India and other Asian countries. Our working flow is: received inquiry->start sourcing->(in 1 week time)give price and delivery date on inquired products or further information->(if needed)arrange samples for clients->(if samples and orders are confirmed)deliver Pre-production sample-> kick-off production->arrange inspection through the whole production-> (if need) arrange shipment to client. We would like to show the work flow in a personalized way , eg. personalize icons etc.;

4. What kind of product we can source and produce: our business is sourcing and managing manufacture overseas for our clients, product categories mainly, but not just, are clothing, shoes , bags, clothing accessories, makeup accessories, festival or promotional gifts etc. all kind of daily use products . We basically are able to source and manage production of every kind of products with no limits. We would like this page to be particularly personalized in a way to give impression to whom browse our website feel free to send inquiry of any kind of production to us and they can trust us that we will do our job professionally and dynamically. We are thinking of using some icons of daily use products to show our sourcing category , it's just our though so please feel free to propose any other ides that you think is more suitable from the point of view of professional designer.

5. Start an enquiry: here we need to land on a questionary page to let who would like to make en enquiry leave the main information , including:
-Name & Sir name:
-Company name:
-Contact email:
-Phone numer:
-Enquired product:
-Upload image:
-Preferred or previous production country:
-Preferred price: FOB, CIF, DDP
-If CIF or DDP where the arrival port/airport will be:
-Preferred delivery time:
-Preferred transportation: by air, by sea, by train
- Other specific requires:

6: Contact us: We will supply contact info later on

Above are our thoughts but please feel free to propose any other ideas that you think should be more suitable for us. We trust your expertise and professional opinions.

Wholesalers and retailers who need to produce their products overseas (mainly in China and other countries in Asia)

• We think it will be nice to show information in simple and comprehensive icons instead of piles of words. We will want our website neat, easy to understand what we do and professional. However this is just our thought so please feel free to propose any other ideas that you think is more suitable from the point of view of professional designer.

```html
<!DOCTYPE html>
<html lang="en">
<head>
<meta charset="utf-8">
<title>Harbourline – Global sourcing and trading</title>
<link href="https://fonts.googleapis.com/css2?family=Fira+Sans:wght@400;500;600&family=Fira+Sans+Condensed:wght@500&display=swap" rel="stylesheet">
<style>
:root{
  --orange:#ec8a24;
  --orange-soft:#f3a14a;
  --teal:#3fb1c3;
  --teal-dark:#2e98a9;
  --ink:#333;
  --muted:#666;
  --line:#dcdcdc;
  --topbar:#e6e6e6;
  --dark:#222;
  --white:#fff;
}
*{box-sizing:border-box;margin:0;padding:0}
html,body{width:1200px;height:3430px;overflow:hidden}
body{font-family:"Fira Sans",Arial,sans-serif;color:var(--ink);background:var(--white);position:relative}
.wrap{width:911px;margin-left:144px;position:relative}

.topbar{height:36px;background:var(--topbar);font-size:11px;color:#333;display:flex;align-items:center;justify-content:center}

.header{height:83px;display:flex;align-items:center}
.header .wrap{display:flex;align-items:center;height:83px}
.brand{display:flex;align-items:center;gap:12px}
.brand-dot{width:40px;height:40px;border-radius:50%;background:var(--teal)}
.brand-text{display:flex;flex-direction:column}
.brand-name{font-size:34px;font-weight:500;color:var(--orange);line-height:1}
.brand-tag{font-size:15px;font-weight:500;color:var(--teal);margin-top:3px}
.nav{display:flex;position:absolute;left:368px;top:0;height:83px;align-items:center;gap:0}
.nav a{font-size:13px;color:#444;text-decoration:none;margin-right:33px}
.nav a.active{color:var(--teal)}
.btn-enquiry{position:absolute;left:776px;top:24px;width:135px;height:35px;border:1px solid var(--orange);color:var(--orange);font-size:13px;display:flex;align-items:center;justify-content:center;text-decoration:none}

.hero{position:relative;height:587px;overflow:hidden}
.hero-photo{position:absolute;inset:0;background:linear-gradient(180deg,#3a4a66 0%,#8a6a50 35%,#e79a3a 55%,#b5532c 75%,#3a2f3a 100%)}
.hero-curve{position:absolute;left:0;bottom:0;width:1200px;height:140px}
.hero-caption{position:absolute;left:600px;top:228px;transform:translateX(-50%);height:44px;padding:0 12px;background:rgba(210,120,30,.92);color:var(--white);font-family:"Fira Sans Condensed","Fira Sans",Arial,sans-serif;font-size:26px;font-weight:500;white-space:nowrap;display:flex;align-items:center;justify-content:center}
.hero-arrow{position:absolute;top:238px;width:20px;height:20px}
.hero-arrow.prev{left:58px}
.hero-arrow.next{left:1122px}

.about{height:390px;position:relative}
.about h2{position:absolute;left:144px;top:80px;font-size:40px;font-weight:500;color:var(--orange)}
.about p{position:absolute;left:144px;top:134px;width:420px;font-size:18px;line-height:32px;color:#333}
.btn-more{position:absolute;left:144px;top:269px;width:96px;height:40px;background:var(--teal);color:var(--white);font-size:13px;display:flex;align-items:center;justify-content:center;border-radius:2px}
.about-photo{position:absolute;left:642px;top:82px;width:414px;height:228px;background:linear-gradient(160deg,#f3b04a 0%,#c2703a 40%,#5a6f86 70%,#2f4a6a 100%)}

.workflow{height:672px;position:relative;background:linear-gradient(180deg,#ee8a23 0%,#ef9a45 55%,#e47e2c 80%,#d06a22 100%)}
.workflow h2{position:absolute;left:0;right:0;top:72px;text-align:center;font-size:40px;font-weight:500;color:var(--white)}
.steps{position:absolute;left:144px;top:143px;width:911px;display:grid;grid-template-columns:repeat(4,217px);column-gap:14.6px;row-gap:14px;grid-template-rows:240px 208px}
.step{background:var(--white);position:relative;text-align:center;padding-top:22px}
.step-num{position:absolute;left:0;top:0;width:27px;height:27px;background:#333;color:var(--white);font-size:13px;font-weight:500;border-radius:0 0 14px 0;display:flex;align-items:center;justify-content:center}
.step svg{width:58px;height:58px;stroke:#444;fill:none;stroke-width:1.6}
.step p{font-size:19px;line-height:30.5px;color:#444;padding:8px 14px 0}

.products{height:707px;position:relative}
.products h2{position:absolute;left:0;right:0;top:74px;text-align:center;font-size:40px;font-weight:500;color:var(--orange)}
.cat-grid{position:absolute;left:144px;top:141px;display:grid;grid-template-columns:repeat(3,297px);column-gap:10px;row-gap:0}
.cat{height:256px}
.cat-photo{height:192px}
.cat h3{font-size:20px;font-weight:500;color:#444;text-align:center;margin-top:10px}
.p1{background:linear-gradient(135deg,#9aa2b0,#e8e8ea 50%,#2f3a55)}
.p2{background:linear-gradient(135deg,#d8d8da,#6b4a33 55%,#2f3d5a)}
.p3{background:linear-gradient(135deg,#c87a6e,#e3a59a 40%,#1e2430)}
.p4{background:linear-gradient(135deg,#d4b79a,#2a3350 55%,#c9b3a0)}
.p5{background:linear-gradient(135deg,#f3f1ef,#d9c2ad 50%,#333)}
.p6{background:linear-gradient(135deg,#d9a8a0,#f4f4f4 45%,#8a8a8a)}

.enquiry{height:563px;position:relative;background:var(--teal)}
.enquiry h2{position:absolute;left:0;right:0;top:70px;text-align:center;font-size:40px;font-weight:500;color:var(--white)}
.form{position:absolute;left:144px;top:144px;width:911px;display:grid;grid-template-columns:repeat(4,217px);column-gap:14.6px;row-gap:18px}
.field{height:38px;background:var(--white);font-size:11px;color:#444;padding:0 10px;display:flex;align-items:center;justify-content:space-between;border:1px solid #e4e4e4;white-space:nowrap;overflow:hidden}
.field.tight{font-size:10px;padding:0 8px;letter-spacing:-.1px}
.field .caret{width:0;height:0;border-left:6px solid transparent;border-right:6px solid transparent;border-top:7px solid #222}
.field.area{grid-column:1 / 5;height:110px;align-items:flex-start;padding-top:14px}
.btn-submit{position:absolute;left:553px;top:443px;width:94px;height:39px;background:#1f1f1f;color:var(--white);font-size:13px;display:flex;align-items:center;justify-content:center}

.contact{height:296px;position:relative}
.contact h2{position:absolute;left:0;right:0;top:72px;text-align:center;font-size:40px;font-weight:500;color:var(--orange)}
.pills{position:absolute;left:144px;top:137px;display:grid;grid-template-columns:repeat(3,297px);column-gap:10px}
.pill{height:79px;border:1px solid #cfcfcf;border-radius:40px;display:flex;align-items:center;padding-left:8px;gap:16px;overflow:hidden}
.pill-icon{width:61px;height:61px;border-radius:50%;background:#dedede;display:flex;align-items:center;justify-content:center;flex:none}
.pill-icon svg{width:22px;height:22px;fill:#777}
.pill span{font-size:18px;color:#444;white-space:nowrap}
.pill span.small{font-size:13px;line-height:19px}

.footer{position:absolute;left:0;top:3334px;width:1200px;height:96px;background:var(--dark)}
.footer-links{position:absolute;left:144px;top:30px;font-size:12px;color:#aaa}
.footer-links a{color:#aaa;text-decoration:none}
.footer-links i{font-style:normal;margin:0 9px}
.copyright{position:absolute;left:144px;top:62px;font-size:12px;color:#aaa}
.social{position:absolute;left:990px;top:40px;display:flex;gap:22px}
.social span{width:20px;height:20px;border-radius:50%;background:#888}
</style>
</head>
<body>

<div class="topbar">Introducing our competence on managing sourcing and overseas production under the travel restriction and the growing tension on global trading.</div>

<header class="header">
  <div class="wrap">
    <div class="brand">
      <span class="brand-dot"></span>
      <div class="brand-text">
        <span class="brand-name">Harbourline</span>
        <span class="brand-tag">Global sourcing and trading</span>
      </div>
    </div>
    <nav class="nav">
      <a class="active" href="#">Home</a>
      <a href="#">About Us</a>
      <a href="#">Services</a>
      <a href="#">Products</a>
      <a href="#">Contact Us</a>
    </nav>
    <a class="btn-enquiry" href="#">Start an enquiry</a>
  </div>
</header>

<section class="hero">
  <div class="hero-photo" role="img" aria-label="Sunset over a cargo port with container stacks, a truck, a ship and a plane overhead"></div>
  <div class="hero-caption">Let us handle the overseas sourcing and production for you</div>
  <svg class="hero-arrow prev" viewBox="0 0 20 20"><path d="M13 2 L5 10 L13 18" stroke="#fff" stroke-width="2.5" fill="none"/></svg>
  <svg class="hero-arrow next" viewBox="0 0 20 20"><path d="M7 2 L15 10 L7 18" stroke="#fff" stroke-width="2.5" fill="none"/></svg>
  <svg class="hero-curve" viewBox="0 0 1200 140" preserveAspectRatio="none">
    <path d="M0,140 L0,40 Q600,150 1200,28 L1200,140 Z" fill="#3fb1c3"/>
    <path d="M0,140 L0,50 Q600,175 1200,40 L1200,140 Z" fill="#fff"/>
  </svg>
</section>

<section class="about">
  <h2>About us</h2>
  <p>We are a professional team with mature global sourcing and trading experience. We have branch office in Hong Kong and local resources around all areas in China , India and other Asian countries.</p>
  <a class="btn-more">Read More</a>
  <div class="about-photo" role="img" aria-label="Aerial view of a container port at sunrise"></div>
</section>

<section class="workflow" role="region" aria-label="Work flow over a faint harbour scene">
  <h2>Work Flow</h2>
  <div class="steps">
    <div class="step"><span class="step-num">1</span>
      <svg viewBox="0 0 58 58"><path d="M16 6h20l8 8v38H16z"/><path d="M36 6v8h8"/><path d="M21 22h16M21 28h16M21 34h12M21 40h8"/><path d="M44 30l-12 14-3 6 6-3 12-14z"/></svg>
      <p>Received inquiry</p></div>
    <div class="step"><span class="step-num">2</span>
      <svg viewBox="0 0 58 58"><circle cx="29" cy="29" r="24"/><path d="M21 19a14 14 0 1 0 16 0"/><path d="M29 14v15"/></svg>
      <p>Start sourcing</p></div>
    <div class="step"><span class="step-num">3</span>
      <svg viewBox="0 0 58 58"><rect x="6" y="10" width="46" height="42" rx="3"/><path d="M6 20h46M16 5v9M42 5v9"/><circle cx="16" cy="28" r="2"/><circle cx="25" cy="28" r="2"/><circle cx="34" cy="28" r="2"/><circle cx="43" cy="28" r="2"/><circle cx="16" cy="37" r="2"/><circle cx="25" cy="37" r="2"/><circle cx="34" cy="37" r="2"/><circle cx="43" cy="37" r="2"/><circle cx="16" cy="45" r="3"/><path d="M14.5 45l1.2 1.2 2-2.4"/></svg>
      <p>Give price and delivery date on inquired products or further information</p></div>
    <div class="step"><span class="step-num">4</span>
      <svg viewBox="0 0 58 58"><path d="M6 20h46l-4 30H10z"/><path d="M12 20V6h22l6 6v8"/><path d="M16 14V10M18 14h16"/></svg>
      <p>Arrange samples for clients</p></div>
    <div class="step"><span class="step-num">5</span>
      <svg viewBox="0 0 58 58"><path d="M14 8h26v44H14z"/><path d="M18 4h26v44"/><path d="M19 18h16M19 24h16M19 30h16M19 36h16M19 42h10"/></svg>
      <p>Deliver Pre-production sample</p></div>
    <div class="step"><span class="step-num">6</span>
      <svg viewBox="0 0 58 58"><circle cx="22" cy="22" r="12" stroke-dasharray="4 3"/><circle cx="22" cy="22" r="5"/><circle cx="40" cy="40" r="10" stroke-dasharray="4 3"/><circle cx="40" cy="40" r="4"/></svg>
      <p>Kick-off production</p></div>
    <div class="step"><span class="step-num">7</span>
      <svg viewBox="0 0 58 58"><circle cx="22" cy="20" r="13" stroke-dasharray="5 3"/><circle cx="22" cy="20" r="6"/><circle cx="20" cy="42" r="9" stroke-dasharray="4 3"/><circle cx="20" cy="42" r="3"/><circle cx="42" cy="38" r="9" stroke-dasharray="4 3"/><circle cx="42" cy="38" r="3"/></svg>
      <p>Arrange inspection through the whole production</p></div>
    <div class="step"><span class="step-num">8</span>
      <svg viewBox="0 0 58 58"><path d="M6 52h46"/><rect x="8" y="30" width="22" height="22"/><path d="M12 34v14M17 34v14M22 34v14M26 34v14"/><path d="M36 52V10h8v42"/><path d="M40 10v-4M36 20h-22v10"/><rect x="44" y="28" width="8" height="24"/></svg>
      <p>Arrange shipment to client</p></div>
  </div>
</section>

<section class="products">
  <h2>Product Categories</h2>
  <div class="cat-grid">
    <div class="cat"><div class="cat-photo p1" role="img" aria-label="Flat lay of trousers, scarf, watch, shoes and jacket"></div><h3>Clothing</h3></div>
    <div class="cat"><div class="cat-photo p2" role="img" aria-label="Leather shoes and a belt"></div><h3>Shoes</h3></div>
    <div class="cat"><div class="cat-photo p3" role="img" aria-label="Hands holding a dark leather handbag"></div><h3>Bags</h3></div>
    <div class="cat"><div class="cat-photo p4" role="img" aria-label="Tailor sewing buttons on a navy jacket"></div><h3>Clothing Accessories</h3></div>
    <div class="cat"><div class="cat-photo p5" role="img" aria-label="Makeup brushes, lipstick and powder compacts"></div><h3>Makeup Accessories</h3></div>
    <div class="cat"><div class="cat-photo p6" role="img" aria-label="Hands tying a ribbon on a white gift box"></div><h3>Festival or Promotional Gifts</h3></div>
  </div>
</section>

<section class="enquiry" role="region" aria-label="Enquiry form over a faint trucking yard scene">
  <h2>Start an enquiry</h2>
  <div class="form">
    <div class="field">Name</div>
    <div class="field">Sir name</div>
    <div class="field">Company name</div>
    <div class="field">Contact email</div>
    <div class="field">Phone numer</div>
    <div class="field">Enquired product</div>
    <div class="field">Upload image</div>
    <div class="field tight">Preferred or previous production country</div>
    <div class="field">Preferred price <span class="caret"></span></div>
    <div class="field">Arrival port/airport will be</div>
    <div class="field">Preferred delivery time</div>
    <div class="field">Preferred transportation <span class="caret"></span></div>
    <div class="field area">Other specific requires</div>
  </div>
  <div class="btn-submit">Submit</div>
</section>

<section class="contact">
  <h2>Contact Us</h2>
  <div class="pills">
    <div class="pill">
      <span class="pill-icon"><svg viewBox="0 0 24 24"><path d="M12 2a7 7 0 0 0-7 7c0 5 7 13 7 13s7-8 7-13a7 7 0 0 0-7-7zm0 9.5A2.5 2.5 0 1 1 12 6.5a2.5 2.5 0 0 1 0 5z"/></svg></span>
      <span class="small">24 Building name, Street name,<br>City Zipcode</span>
    </div>
    <div class="pill">
      <span class="pill-icon"><svg viewBox="0 0 24 24"><path d="M6.6 10.8a15 15 0 0 0 6.6 6.6l2.2-2.2a1 1 0 0 1 1-.25 11.4 11.4 0 0 0 3.6.6 1 1 0 0 1 1 1V20a1 1 0 0 1-1 1A17 17 0 0 1 3 4a1 1 0 0 1 1-1h3.5a1 1 0 0 1 1 1c0 1.25.2 2.45.6 3.6a1 1 0 0 1-.25 1z"/></svg></span>
      <span>555 014 2290</span>
    </div>
    <div class="pill">
      <span class="pill-icon"><svg viewBox="0 0 24 24"><path d="M2 6h20v12H2z" fill="none" stroke="#777" stroke-width="2"/><path d="M2 6l10 7 10-7" fill="none" stroke="#777" stroke-width="2"/></svg></span>
      <span>info@harbourline.co</span>
    </div>
  </div>
</section>

<footer class="footer">
  <div class="footer-links">
    <a href="#">Home</a><i>|</i><a href="#">About Us</a><i>|</i><a href="#">Services</a><i>|</i><a href="#">Products</a><i>|</i><a href="#">Contact Us</a><i>|</i><a href="#">Start an enquiry</a>
  </div>
  <div class="copyright">Copyright © 2020 &nbsp;Harbourline. &nbsp;All rights reserved.</div>
  <div class="social"><span></span><span></span></div>
</footer>

</body>
</html>
```